Bramblewood Joinery Website

My client Bramblewood Joinery is looking for a redesign for a Word Press Website. Their current site is at www.bramblewoodjoinery.example They are a custom cabinet company, but also create bathroom, living room, bar and entertainment and bedroom cabinets too. They would like a design that emulates the master craftsman work they do yet a contemporary style.

Their current site was designed using Flash elements.

Target Market(s)

Home owners and builders of high end homes

Industry/Entity Type

Entertainment

Font styles to use
Serif
Decorative

Requirements
Must have
• Must show their work and logo using a contemporary style.
Nice to have
• Sliders that showcase their projects.

```html
<!DOCTYPE html>
<html lang="en">
<head>
<meta charset="utf-8">
<title>Bramblewood Joinery</title>
<link href="https://fonts.googleapis.com/css2?family=Open+Sans:wght@300;400;600;700&display=swap" rel="stylesheet">
<style>
:root{
  --green:#3db53f;
  --dark:#4a4a4a;
  --black:#111;
  --footer:#3a3a3a;
  --bottom:#2e2e2e;
  --light:#f4f4f4;
  --card:#e6e6e6;
  --text:#333;
  --muted:#999;
}
*{margin:0;padding:0;box-sizing:border-box}
html,body{width:794px;height:1200px;overflow:hidden}
body{position:relative;font-family:"Open Sans",sans-serif;color:var(--text);background:#fff}
.abs{position:absolute}
.topbar{left:0;top:0;width:794px;height:24px;background:var(--black);color:#ddd;font-size:9px}
.topbar .contact{left:172px;top:6px;word-spacing:1px}
.topbar .contact span{margin-right:14px}
.topbar .links{right:74px;top:6px}
.topbar .links i{font-style:normal;margin:0 6px;color:#aaa}
.header{left:0;top:24px;width:794px;height:60px;background:#fff}
.logo{left:72px;top:4px;width:96px;height:96px;border-radius:50%;background:#fff;border:3px solid #111;display:flex;align-items:center;justify-content:center;text-align:center;font-size:11px;font-weight:700;color:#111;line-height:1.2;z-index:3}
.nav{right:72px;top:22px;display:flex;gap:30px;font-size:11px;color:#555}
.nav .active{color:var(--green);font-weight:600;position:relative}
.nav .active::before{content:"";position:absolute;left:-4px;right:-4px;top:-24px;height:2px;background:var(--green)}
.hero{left:0;top:84px;width:794px;height:342px;background:linear-gradient(180deg,#cfc7b6 0%,#b9ad98 45%,#7a5a40 75%,#5a3c28 100%)}
.hero-box{left:73px;top:195px;width:302px;height:115px;background:rgba(0,0,0,.72);color:#fff;padding:9px 11px}
.hero-box h1{font-weight:300;font-size:22px;line-height:1.1;margin-bottom:5px}
.hero-box h1 b{font-weight:700}
.hero-box p{font-size:9.6px;line-height:1.28}
.hero-box a{display:inline-block;margin-top:7px;font-size:9.6px;color:#fff;text-decoration:underline;font-weight:600}
.room{border-radius:50%;color:#fff;text-align:center;display:flex;flex-direction:column;align-items:center;justify-content:center}
.room h2{font-size:12px;font-weight:600;padding:0 12px 2px;border-bottom:1px solid #fff;margin-bottom:8px}
.room p{font-size:8.6px;font-weight:600;line-height:1.55}
.room.grey{background:var(--dark);width:166px;height:166px}
.room.green{background:var(--green);width:204px;height:204px}
.badge{width:60px;height:60px;border-radius:50%;background:#fff;border:3px solid #fff;box-shadow:0 0 0 1px #555 inset;display:flex;align-items:center;justify-content:center}
.badge.green{background:var(--green);box-shadow:0 0 0 3px #fff inset}
.portfolio{left:0;top:701px;width:794px;height:334px;background:var(--light)}
.portfolio h2{position:absolute;top:28px;left:0;width:794px;text-align:center;font-size:19px;font-weight:600;color:#333;letter-spacing:.5px}
.portfolio .rule{position:absolute;top:41px;height:1px;background:#ddd}
.portfolio .sub{position:absolute;top:58px;width:794px;text-align:center;font-size:9.2px;color:#555}
.card{top:111px;width:202px;height:192px;background:var(--card);text-align:center}
.card .photo{height:132px}
.card h3{font-size:10.5px;font-weight:400;margin-top:13px;color:#333}
.card a{display:inline-block;margin-top:8px;font-size:10px;color:var(--muted);text-decoration:underline}
.card.active{background:var(--green)}
.card.active h3,.card.active a{color:#fff}
.footer{left:0;top:1035px;width:794px;height:126px;background:var(--footer)}
.footer .join{left:74px;top:42px;font-size:10.5px;color:#ddd}
.footer .field{left:74px;top:61px;width:287px;height:22px;background:#fff;border:1px solid #ccc;font-size:9.5px;font-style:italic;color:#777;padding:4px 6px}
.footer .btn{left:369px;top:61px;width:72px;height:22px;background:var(--green);color:#fff;font-size:10.5px;font-weight:600;text-align:center;line-height:22px}
.social{left:524px;top:62px;display:flex;gap:20px}
.social .ic{width:24px;height:24px;display:flex;align-items:center;justify-content:center}
.bottom{left:0;top:1161px;width:794px;height:39px;background:var(--bottom);color:#aaa;font-size:8.6px}
.bottom .copy{left:75px;top:15px}
.bottom .legal{right:71px;top:15px}
.bottom .legal i{font-style:normal;margin:0 7px}
</style>
</head>
<body>
<div class="abs topbar">
  <div class="abs contact"><span>Call Us: 555.014.2280</span><span>E-mail: info@bramblewoodjoinery.example</span></div>
  <div class="abs links">Contact Us<i>|</i>Customer Experience<i>|</i>Professional</div>
</div>
<div class="abs header">
  <nav class="abs nav"><span class="active">Home</span><span>Who We Are</span><span>Getting Started</span><span>Portfolio</span><span>Cabinet Hardware</span></nav>
</div>
<div class="abs logo">Bramblewood<br>Joinery</div>

<div class="abs hero" role="img" aria-label="Photo of a bright kitchen with cream cabinets, a dark island and wooden floor"></div>
<div class="abs hero-box">
  <h1>WELCOME TO <b>BRAMBLEWOOD</b></h1>
  <p>Lorem ipsum dolor sit amet consectetur the adipscing elit sed do eiusmod tempor incididunt ut labore et dozilore magna aliqua ut enim ad minim veniam quis nostrud exercitation ullamco laboris aliquip commodo consequat.</p>
  <a>Read More</a>
</div>

<div class="abs room grey" style="left:89px;top:483px">
  <h2>BEDROOM</h2>
  <p>Lorem ipsum dolor sit amet<br>consectetur adipiscing elit<br>Ut quis fermentum sem<br>estibulum tetur adipiUt quitum<br>sem estibulum</p>
</div>
<div class="abs room green" style="left:292px;top:464px">
  <h2>KITCHEN</h2>
  <p>Lorem ipsum dolor sit amet adipi-<br>scing elit, sed do eiusmod tempor<br>incididunt ut labore et dolore<br>magna aliqua enim ad minim<br>veniam, quis nostrud exercitation<br>ullamco laboris nisi</p>
</div>
<div class="abs room grey" style="left:534px;top:483px">
  <h2>BATHROOM</h2>
  <p>Lorem ipsum dolor sit amet<br>consectetur adipiscing elit<br>Ut quis fermentum sem<br>estibulum tetur adipiUt quis<br>fermentum</p>
</div>
<div class="abs badge" style="left:199px;top:468px">
  <svg width="28" height="28" viewBox="0 0 28 28" fill="#444"><path d="M4 8 Q14 0 24 8 V22 H4Z"/><rect x="13" y="6" width="2" height="16" fill="#fff"/><rect x="4" y="15" width="20" height="2" fill="#fff"/><rect x="5" y="22" width="3" height="3"/><rect x="20" y="22" width="3" height="3"/></svg>
</div>
<div class="abs badge green" style="left:434px;top:454px">
  <svg width="28" height="28" viewBox="0 0 28 28" fill="#fff"><rect x="2" y="2" width="11" height="10"/><rect x="15" y="2" width="11" height="5"/><rect x="15" y="9" width="11" height="17"/><rect x="2" y="14" width="11" height="12"/></svg>
</div>
<div class="abs badge" style="left:644px;top:468px">
  <svg width="30" height="24" viewBox="0 0 30 24" fill="#444"><rect x="1" y="3" width="28" height="3"/><rect x="3" y="6" width="24" height="14"/><rect x="10" y="8" width="10" height="3" fill="#fff"/><rect x="4" y="20" width="2" height="3"/><rect x="24" y="20" width="2" height="3"/></svg>
</div>

<section class="abs portfolio">
  <div class="rule" style="left:0;width:316px"></div>
  <div class="rule" style="left:478px;width:316px"></div>
  <h2>OUR PORTFILO</h2>
  <p class="sub">If we can use our images across the site, we can add this at a later date when we have completed more projects.</p>
  <div class="abs card" style="left:73px">
    <div class="photo" role="img" aria-label="Photo of a white kitchen with stove and sunflowers" style="background:linear-gradient(180deg,#e8e4dc,#b7ab98 70%,#6b4a34)"></div>
    <h3>kitchens Cabinet</h3><a>View more</a>
  </div>
  <div class="abs card active" style="left:297px">
    <div class="photo" role="img" aria-label="Photo of a bedroom with wall-to-wall wooden wardrobes" style="background:linear-gradient(180deg,#9a6a3c,#d19a5a 45%,#b9834b 75%,#2c3a55)"></div>
    <h3>Bedroom Cabinet</h3><a>View more</a>
  </div>
  <div class="abs card" style="left:520px">
    <div class="photo" role="img" aria-label="Photo of a bathroom with freestanding tub and vanity" style="background:linear-gradient(180deg,#8a8a7e,#c8c3b6 55%,#e2ded4)"></div>
    <h3>Bathroom Cabinet</h3><a>View more</a>
  </div>
</section>

<footer class="abs footer">
  <div class="abs join">Join 8,000 Smart Owners Who Get Our Emails Every Month. Be Better In 2014.</div>
  <div class="abs field">Enter your Email</div>
  <div class="abs btn">SUBCRIBE</div>
  <div class="abs social">
    <div class="ic"><svg width="16" height="24" viewBox="0 0 16 24" fill="none" stroke="#fff" stroke-width="2"><rect x="2" y="1" width="12" height="22" rx="2"/><line x1="2" y1="18" x2="14" y2="18"/></svg></div>
    <div class="ic"><svg width="22" height="22"><circle cx="11" cy="11" r="10" fill="#fff"/></svg></div>
    <div class="ic"><svg width="22" height="22"><rect x="1" y="1" width="20" height="20" rx="3" fill="#fff"/></svg></div>
    <div class="ic"><svg width="22" height="22"><circle cx="11" cy="11" r="10" fill="#fff"/></svg></div>
    <div class="ic"><svg width="24" height="22" viewBox="0 0 24 22" fill="none" stroke="#fff" stroke-width="2"><rect x="2" y="2" width="20" height="18"/><path d="M2 2 L12 12 L22 2 M2 20 L10 11 M22 20 L14 11"/></svg></div>
  </div>
</footer>
<div class="abs bottom">
  <div class="abs copy">Copyrights © 2015 Bramblewood Joinery  - All Rights Reserved</div>
  <div class="abs legal">Privacy Policy<i>|</i>Term &amp; Conditions</div>
</div>
</body>
</html>
```